Hvac and insulation company needs good looking business card design

We are hvac and insulation company and looking for a new business cards that look to today standards designs

Target Market(s)

homeowners

Industry/Entity Type

Hvac

Contact Information for Business Card

Name: Walter Brinoku
Home comfort consultant
address: 4827 Dunmore St #215 Oakland, CA 94619
office: 888-316-2790
cell: 510-742-3185
Lic.# 584261
Email: walter@corvane-hvac.com
Web: corvane-hvac.com

Requirements
Must have
• clean and sleek look
Nice to have
• simple with a clean look
Should not have
• to busy business card

```html
<!DOCTYPE html>
<html lang="en">
<head>
<meta charset="utf-8">
<title>Corvane Home Solutions – Business Card</title>
<link href="https://fonts.googleapis.com/css2?family=Rubik:wght@400;500&display=swap" rel="stylesheet">
<style>
  :root{
    --orange:#ee7d1f;
    --orange-dark:#c9661a;
    --slate:#6b6d6e;
    --slate-light:#8a8c8d;
    --ink:#55585a;
    --paper:#ffffff;
    --backdrop:#e4e5e6;
  }
  *{box-sizing:border-box;margin:0;padding:0}
  html,body{width:1200px;height:900px;overflow:hidden}
  body{background:var(--backdrop);font-family:"Rubik",Arial,sans-serif;position:relative}
  .card{position:absolute;width:620px;height:354px;border-radius:18px;overflow:hidden;box-shadow:0 10px 30px rgba(0,0,0,.18)}
  .card--front{left:290px;top:64px;background:var(--paper)}
  .card--back{left:290px;top:482px;background:linear-gradient(135deg,#737576,#5d5f60)}
  .card__swoosh{position:absolute;inset:0}
  .brand{position:absolute;display:flex;align-items:center;gap:10px}
  .brand__mark{width:30px;height:30px;background:var(--orange);border-radius:4px}
  .brand__name{color:var(--orange);font-weight:500;font-size:46px;line-height:1;letter-spacing:-.5px}
  .brand__tag{color:var(--slate-light);font-size:14px;letter-spacing:3px}
  .card--front .brand{left:38px;top:46px}
  .card--front .brand__tag{position:absolute;left:78px;top:88px}
  .rule{position:absolute;height:1.5px;background:var(--orange)}
  .rule--contacts{left:38px;top:128px;width:300px}
  .contacts{position:absolute;left:38px;top:152px;list-style:none;font-size:15px;color:var(--ink);line-height:25px}
  .contacts li{display:flex;align-items:center;gap:9px}
  .contacts svg{width:11px;height:11px;flex:none}
  .contacts .accent{color:var(--orange)}
  .person{position:absolute;right:36px;top:196px;width:260px}
  .person__name{color:var(--orange);font-size:22px;font-weight:500;text-transform:uppercase;letter-spacing:.3px;white-space:nowrap}
  .person__role{color:var(--ink);font-size:15px;margin-top:2px}
  .rule--person{right:36px;top:256px;width:260px}
  .address{position:absolute;right:36px;top:272px;width:260px;font-size:14px;color:var(--ink);line-height:20px}
  .card--back .brand{left:150px;top:120px}
  .card--back .brand__mark{width:40px;height:40px}
  .card--back .brand__name{font-size:66px}
  .card--back .brand__tag{position:absolute;left:204px;top:196px;color:#b9bbbc;font-size:18px;letter-spacing:4px}
  .license{position:absolute;left:230px;top:262px;color:#d9dadb;font-size:18px;letter-spacing:1px}
</style>
</head>
<body>
  <section class="card card--front">
    <svg class="card__swoosh" viewBox="0 0 620 354" aria-hidden="true">
      <path d="M235,0 C360,6 400,50 455,88 C515,122 570,124 620,124 L620,0 Z" fill="#6a6c6d"/>
      <path d="M205,0 C320,6 350,30 380,60" fill="none" stroke="#9b9d9e" stroke-width="6"/>
      <path d="M190,0 C330,6 380,60 440,100 C500,138 560,142 620,142" fill="none" stroke="var(--orange)" stroke-width="12"/>
    </svg>
    <div class="brand">
      <span class="brand__mark"></span>
      <span class="brand__name">corvane</span>
    </div>
    <span class="brand__tag">home solutions</span>
    <div class="rule rule--contacts"></div>
    <ul class="contacts">
      <li><svg viewBox="0 0 12 12"><path d="M3 1l2 2-1 1.5c.6 1.4 1.6 2.4 3 3L8.5 6.5l2 2L9 10.5C5 10 2 7 1.5 3z" fill="var(--orange)"/></svg>888-316-2790</li>
      <li><svg viewBox="0 0 12 12"><rect x="3" y="1" width="6" height="10" rx="1.2" fill="none" stroke="var(--orange)" stroke-width="1.5"/></svg>510-742-3185</li>
      <li><svg viewBox="0 0 12 12"><rect x="1" y="2.5" width="10" height="7" fill="none" stroke="var(--orange)" stroke-width="1.3"/><path d="M1 2.5l5 4 5-4" fill="none" stroke="var(--orange)" stroke-width="1.3"/></svg>walter@corvane-hvac.com</li>
      <li><svg viewBox="0 0 12 12"><circle cx="6" cy="6" r="5" fill="var(--orange)"/></svg><span>www.<span class="accent">corvane-hvac</span>.com</span></li>
    </ul>
    <div class="person">
      <p class="person__name">Walter Brinoku</p>
      <p class="person__role">Home comfort consultant</p>
    </div>
    <div class="rule rule--person"></div>
    <p class="address">4827 Dunmore St<br>#215 Oakland, CA 94619</p>
  </section>

  <section class="card card--back">
    <div class="brand">
      <span class="brand__mark"></span>
      <span class="brand__name">corvane</span>
    </div>
    <span class="brand__tag">home solutions</span>
    <p class="license">Lic.# 584261</p>
  </section>
</body>
</html>
```